wealth management firm, professional group, new model

we have a logo that works but we need a card, white background using our colors...clean look

our tag line if can be used in

The Pathway From Saving to Legacy

```html
<!DOCTYPE html>
<html lang="en">
<head>
<meta charset="utf-8">
<title>Veraline Wealth Partners – Business Card</title>
<link href="https://fonts.googleapis.com/css2?family=Cinzel:wght@700&family=Montserrat:wght@400;700&family=Poppins:wght@400&display=swap" rel="stylesheet">
<style>
  :root {
    --navy-deep: #111d38;
    --navy-mid: #14264a;
    --navy-light: #1d3766;
    --white: #ffffff;
    --silver: #b9b9b9;
    --stage: #dddddd;
    --icon: #c9cbd1;
  }
  * { margin: 0; padding: 0; box-sizing: border-box; }
  html, body { width: 892px; height: 1200px; overflow: hidden; }
  body { background: var(--stage); position: relative; font-family: "Montserrat", sans-serif; }

  .card {
    position: absolute; left: 90px; width: 712px; height: 407px;
    background: var(--white); overflow: hidden;
    box-shadow: 0 14px 18px rgba(0,0,0,0.28);
  }
  .card--front { top: 157px; }
  .card--back { top: 635px; }

  .front__panel {
    position: absolute; left: 0; top: 0; width: 100%; height: 331px;
    background: radial-gradient(circle at 100% 0%, var(--navy-light) 0%, var(--navy-mid) 45%, var(--navy-deep) 80%);
  }
  .brand-name {
    position: absolute; left: 0; width: 100%; text-align: center;
    font-family: "Montserrat", sans-serif; font-weight: 400; color: var(--white);
  }
  .front__name { top: 152px; font-size: 56px; letter-spacing: 24px; padding-left: 24px; line-height: 1; }
  .front__sub { top: 250px; font-size: 22px; letter-spacing: 4.5px; padding-left: 4px; }

  .front__web {
    position: absolute; left: 0; top: 331px; width: 100%; height: 76px;
    display: flex; align-items: center; justify-content: center;
    font-size: 15px; letter-spacing: 7px; color: var(--navy-deep); padding-left: 7px;
  }
  .front__web strong { font-weight: 700; }

  .back__brand { position: absolute; left: 60px; top: 92px; width: 224px; }
  .back__brand .brand-name { position: static; color: var(--navy-deep); }
  .back__name { font-size: 28px; letter-spacing: 10px; padding-left: 10px; line-height: 1; }
  .back__sub { margin-top: 20px; font-size: 12.5px; letter-spacing: 2.6px; }

  .tagline {
    position: absolute; left: 363px; top: 52px;
    font-family: "Cinzel", serif; font-weight: 700; line-height: 0.86; color: var(--navy-deep);
  }
  .tagline__lead { display: block; font-size: 29px; color: var(--silver); letter-spacing: 0.5px; line-height: 0.95; }
  .tagline__main { display: block; font-size: 43px; letter-spacing: 0.2px; }

  .back__panel {
    position: absolute; left: 65px; top: 186px; width: 647px; height: 193px;
    background: radial-gradient(circle at 100% 0%, var(--navy-light) 0%, var(--navy-mid) 45%, var(--navy-deep) 80%);
  }
  .person { position: absolute; left: 39px; top: 32px; font-family: "Cinzel", serif; font-weight: 700; line-height: 0.88; }
  .person__first { display: block; font-size: 42px; color: var(--white); }
  .person__last { display: block; font-size: 42px; color: var(--silver); }
  .person__rule { position: absolute; left: 39px; top: 121px; width: 108px; height: 1px; background: var(--silver); }
  .person__role {
    position: absolute; left: 39px; top: 133px;
    font-size: 14px; letter-spacing: 4.5px; color: var(--white);
  }

  .contacts { position: absolute; left: 302px; top: 30px; list-style: none; }
  .contacts li {
    display: flex; align-items: center; height: 32px;
    font-family: "Poppins", sans-serif; font-size: 16.5px; color: var(--white);
  }
  .contacts svg { width: 17px; height: 17px; margin-right: 8px; flex: none; }
</style>
</head>
<body>

<section class="card card--front">
  <div class="front__panel">
    <div class="brand-name front__name">VERALINE</div>
    <div class="brand-name front__sub">WEALTH PARTNERS</div>
  </div>
  <div class="front__web">WWW.<strong>VERALINEWEALTH</strong>.COM</div>
</section>

<section class="card card--back">
  <div class="back__brand">
    <div class="brand-name back__name">VERALINE</div>
    <div class="brand-name back__sub">WEALTH PARTNERS</div>
  </div>

  <h2 class="tagline">
    <span class="tagline__lead">THE PATHWAY</span>
    <span class="tagline__main">FROM SAVING</span>
    <span class="tagline__main">TO LEGACY</span>
  </h2>

  <div class="back__panel">
    <div class="person">
      <span class="person__first">DANIEL</span>
      <span class="person__last">HAYES</span>
    </div>
    <div class="person__rule"></div>
    <div class="person__role">OWNER</div>

    <ul class="contacts">
      <li>
        <svg viewBox="0 0 20 20" aria-hidden="true"><circle cx="10" cy="10" r="10" fill="var(--icon)"/><path d="M7 5.5l1.6 0 .8 2.3-1.1.8c.6 1.3 1.6 2.3 2.9 2.9l.8-1.1 2.3.8 0 1.6c0 .6-.5 1-1.1 1C9.4 13.8 6.2 10.6 6 6.6c0-.6.4-1.1 1-1.1z" fill="var(--navy-mid)"/></svg>
        555 0142 0199
      </li>
      <li>
        <svg viewBox="0 0 20 20" aria-hidden="true"><circle cx="10" cy="10" r="10" fill="var(--icon)"/><rect x="5.5" y="7" width="9" height="6.5" rx="0.8" fill="var(--navy-mid)"/><path d="M5.8 7.4L10 10.6l4.2-3.2" stroke="var(--icon)" stroke-width="1" fill="none"/></svg>
        info@veralinewealth.com
      </li>
      <li>
        <svg viewBox="0 0 20 20" aria-hidden="true"><circle cx="10" cy="10" r="10" fill="var(--icon)"/><circle cx="10" cy="10" r="4.6" fill="none" stroke="var(--navy-mid)" stroke-width="1.2"/><path d="M5.4 10h9.2M10 5.4c-2.4 2.6-2.4 6.6 0 9.2M10 5.4c2.4 2.6 2.4 6.6 0 9.2" stroke="var(--navy-mid)" stroke-width="1" fill="none"/></svg>
        www.veralinewealth.com
      </li>
      <li>
        <svg viewBox="0 0 20 20" aria-hidden="true"><circle cx="10" cy="10" r="10" fill="var(--icon)"/><path d="M10 4.8c-2 0-3.4 1.5-3.4 3.3 0 2.4 3.4 6.4 3.4 6.4s3.4-4 3.4-6.4c0-1.8-1.4-3.3-3.4-3.3z" fill="var(--navy-mid)"/><circle cx="10" cy="8.2" r="1.2" fill="var(--icon)"/></svg>
        412 Larkin Avenue Fairhaven
      </li>
    </ul>
  </div>
</section>

</body>
</html>
```